Trucking Company Website Design

We are working with a Trucking company in California. They provide trucking services for dirt, gravel, landscape bark, and landscape materials.

As you might imagine, there are no websites we could find for inspiration for trucking companies.

Thank you for taking the time to consider designing a website for us. We are web developers based in Stockton, CA, USA. Most of our projects go through the same process. Understanding this process may help you win a project with us. We custom-code all of our websites in-house. We don’t have any requirements as to what tools you use for your design, but we ask that you follow these guidelines.

IMAGES:
If you use any images or icons in the design, we ask that you have a link to the asset so we can purchase the image/icon. Most of the designs we submit do not have the customer’s images on them unless they have some great images. Be creative; show us the feeling you are trying to portray with your image choices. Use any royalty-free site you choose. We subscribe to Quillo and mainly use their images, but we can purchase images outside of Quillo. PLEASE NOTE: we will not submit designs to clients with watermarks on the images.

FONTS:
We ask that you identify the fonts you’re using in the design. This can be done in a message if you want. We typically use Varnex Fonts and Quillo Fonts.

CONTENT:
We're always open to different content and ideas. We often submit designs with stock images so the client can see our vision. We typically take pictures after the website launch to use their images with our vision. Lorem Ipsum is fine for paragraphs, but we ask that you make the Headers with correct English. We want to be able to show the vision and identify the sections of the website.

INSPIRATION:
We typically add a couple of links in the brief of websites we like to help you get started in your design.

REVISIONS:
We do not often ask for revisions of the designs unless we see something in the design that may not appeal to the client. If there are slight changes that we want to make, we do that in the development process.

FEEDBACK:
We rarely give feedback on designs during the design process. We are working on many website projects and do not have the time to provide feedback. We usually respond if your request is well thought out and asks specific questions, but a note asking “feedback, please” usually goes unanswered.

```html
<!DOCTYPE html>
<html lang="en">
<head>
<meta charset="utf-8">
<title>Ridgeline Materials</title>
<link href="https://fonts.googleapis.com/css2?family=Teko:wght@400;500&family=Poppins:wght@400&display=swap" rel="stylesheet">
<style>
:root{
  --blue:#5aafd8;
  --navy:#1a74b5;
  --red:#d8222f;
  --ink:#3a3a3a;
  --icon:#1c2b3a;
  --white:#ffffff;
  --footer:#0f0f12;
}
*{box-sizing:border-box;margin:0;padding:0}
html,body{width:1200px;height:3174px;overflow:hidden;background:var(--white)}
body{position:relative;font-family:"Poppins",sans-serif;color:var(--ink)}
.abs{position:absolute}
.display{font-family:"Teko",sans-serif;font-weight:400;text-transform:uppercase;letter-spacing:.5px;line-height:1}

/* hero */
.hero{left:0;top:0;width:1200px;height:595px;background:linear-gradient(180deg,#3b4868 0%,#b0574c 28%,#5c3c45 55%,#262a38 80%,#3b3122 100%)}
.navbar{left:111px;top:28px;width:977px;height:105px;background:var(--white);border-radius:6px}
.brand{display:flex;align-items:center;gap:10px}
.brand-name{font-family:"Teko",sans-serif;font-weight:500;color:var(--navy);font-size:36px;line-height:1;text-transform:uppercase}
.brand-mark{width:26px;height:26px;background:var(--red)}
.navbar .brand{position:absolute;left:26px;top:36px}
.menu{position:absolute;left:398px;top:40px;display:flex;gap:36px}
.menu a{font-family:"Teko",sans-serif;font-size:26px;color:var(--navy);text-decoration:none;text-transform:uppercase;line-height:1}
.menu a.active{color:var(--red)}
.search{position:absolute;right:28px;top:31px;width:42px;height:42px;border-radius:50%;background:var(--blue)}
.hero-title{left:0;top:350px;width:1200px;text-align:center;color:var(--white);font-size:74px}
.hero-rule{left:505px;top:432px;width:190px;height:5px;background:var(--white)}
.hero-sub{left:0;top:464px;width:1200px;text-align:center;color:var(--white);font-size:21px}
.arrow{top:322px}

/* about */
.about-card{left:111px;top:732px;width:520px;height:484px;background:var(--white);border-radius:20px;box-shadow:0 2px 14px rgba(0,0,0,.18)}
.about-photo{left:600px;top:683px;width:488px;height:572px;background:linear-gradient(135deg,#3d5fb8 0%,#8aa0c8 40%,#c9c2c8 60%,#8f96a3 100%)}
.about-title{left:140px;top:792px;width:424px;text-align:right;color:var(--red);font-size:42px}
.about-text{left:120px;top:855px;width:444px;text-align:right;font-size:20px;line-height:35.2px;white-space:nowrap}
.btn{display:flex;align-items:center;justify-content:center;background:var(--blue);color:#1c3d55;font-family:"Teko",sans-serif;font-size:28px;text-transform:uppercase;line-height:1;padding-top:4px}
.btn-tab{position:absolute;right:0;top:0;width:18px;height:100%;background:var(--red)}
.about-btn{left:392px;top:1103px;width:171px;height:40px}

.section-title{left:0;width:1200px;text-align:center;color:var(--red);font-size:42px}

/* services */
.service{width:231px;height:347px;background:var(--white);box-shadow:0 2px 10px rgba(0,0,0,.12);border-bottom:5px solid var(--blue);text-align:center}
.service.featured{background:var(--blue)}
.service-icon{position:absolute;left:71px;top:19px;width:88px;height:88px;border-radius:50%;background:var(--blue)}
.service-icon svg{display:block}
.featured .service-icon{background:var(--white)}
.service-name{position:absolute;left:0;top:137px;width:100%;color:var(--red);font-size:32px;white-space:nowrap}
.featured .service-name,.featured .service-text{color:var(--white)}
.service-text{position:absolute;left:14px;top:170px;width:203px;font-size:20px;line-height:35px;color:var(--ink)}
.plus{position:absolute;left:89px;top:319px;width:52px;height:52px;border-radius:50%;background:var(--blue)}
.featured .plus{background:var(--white);box-shadow:0 2px 6px rgba(0,0,0,.2)}

/* portfolio */
.tile{position:absolute}
.tile-gravel{left:0;top:1955px;width:294px;height:231px;background:linear-gradient(135deg,#8e959c,#c9cdd1 50%,#6d747a)}
.tile-forest{left:297px;top:1955px;width:299px;height:231px;background:linear-gradient(90deg,#5b5650 0%,#6a655c 40%,#4e8a3a 60%,#2f5f26 100%)}
.tile-truck{left:0;top:2188px;width:294px;height:229px;background:linear-gradient(180deg,#9fb9d6 0%,#d8e2ea 35%,#4f7a3c 55%,#6b6d70 100%)}
.tile-soil{left:297px;top:2188px;width:299px;height:229px;background:linear-gradient(180deg,#4e8fd1 0%,#bcd7ee 45%,#5f9a3a 62%,#4a3222 75%,#2e1e14 100%)}
.tile-coast{left:600px;top:1955px;width:600px;height:462px;background:linear-gradient(160deg,#3b4f60 0%,#566a6a 35%,#8d8e84 55%,#394d3c 80%,#2c3a34 100%)}
.zoom{left:872px;top:2162px;width:54px;height:54px;border-radius:50%;background:var(--white)}

/* contact */
.contact-band{left:0;top:2418px;width:1200px;height:164px;background:linear-gradient(120deg,#6b6f70,#5e6363 50%,#6a6e6c)}
.contact-item{display:flex;align-items:center;gap:14px;top:2478px;color:var(--white);font-size:21px;white-space:nowrap}
.contact-icon{width:44px;height:44px;border-radius:50%;background:var(--white);display:flex;align-items:center;justify-content:center}
.field{height:49px;border:none;background:var(--white);box-shadow:0 1px 8px rgba(0,0,0,.12);font-family:"Poppins",sans-serif;font-size:14px;color:#777;padding:15px 13px}
.submit{left:457px;top:2747px;width:171px;height:42px}

/* footer */
.footer{left:0;top:2853px;width:1200px;height:321px;background:var(--footer)}
.footer .brand{position:absolute;left:0;top:65px;width:1200px;justify-content:center}
.footer .brand-name{font-size:48px}
.footer-menu{position:absolute;left:0;top:148px;width:1200px;display:flex;justify-content:center;gap:24px}
.footer-menu a{font-family:"Teko",sans-serif;font-size:26px;color:var(--white);text-decoration:none;text-transform:uppercase;line-height:1}
.socials{position:absolute;left:0;top:207px;width:1200px;display:flex;justify-content:center;gap:12px}
.socials span{width:28px;height:28px;border-radius:50%;background:var(--navy)}
.footer-rule{position:absolute;left:111px;top:269px;width:977px;height:1px;background:#3a3a3e}
.copyright{position:absolute;left:0;top:285px;width:1200px;text-align:center;color:var(--white);font-size:15px}
</style>
</head>
<body>

<section class="abs hero" role="img" aria-label="City skyline at sunset reflected on water"></section>
<header class="abs navbar">
  <div class="brand"><span class="brand-name">Ridgeline Materials</span><span class="brand-mark"></span></div>
  <nav class="menu">
    <a class="active" href="#">Home</a><a href="#">About Us</a><a href="#">Services</a><a href="#">Contact Us</a>
  </nav>
  <div class="search">
    <svg width="42" height="42" viewBox="0 0 42 42"><circle cx="19" cy="19" r="7" fill="none" stroke="#d8222f" stroke-width="2.4"/><line x1="24" y1="24" x2="29" y2="29" stroke="#d8222f" stroke-width="2.4" stroke-linecap="round"/></svg>
  </div>
</header>
<svg class="abs arrow" style="left:92px" width="24" height="30" viewBox="0 0 24 30"><polyline points="17,4 7,15 17,26" fill="none" stroke="#fff" stroke-width="3"/></svg>
<svg class="abs arrow" style="left:1083px" width="24" height="30" viewBox="0 0 24 30"><polyline points="7,4 17,15 7,26" fill="none" stroke="#fff" stroke-width="3"/></svg>
<h1 class="abs display hero-title">Welcome to Ridgeline Materials</h1>
<div class="abs hero-rule"></div>
<p class="abs hero-sub">Lorem ipsum dolor sit amet, consectetur adipiscing elit, et dolore magna aliqua.</p>

<div class="abs about-card"></div>
<div class="abs about-photo" role="img" aria-label="Blue curtain-side truck driving at speed on a highway"></div>
<h2 class="abs display about-title">About Us</h2>
<p class="abs about-text">Sed ut perspiciatis unde omnis iste natus<br>error sit voluptatem accusantium<br>doloremque laudantium, totam rem<br>aperiam, eaque ipsa quae ab illo<br>inventore veritatis et quasi architecto<br>beatae vitae dicta sunt explicabo.</p>
<a class="abs btn about-btn">Learn More<span class="btn-tab"></span></a>

<h2 class="abs display section-title" style="top:1333px">Services</h2>
<div class="abs service" style="left:116px;top:1412px">
  <div class="service-icon">
    <svg width="88" height="88" viewBox="0 0 88 88" fill="none" stroke="#1c2b3a" stroke-width="2" stroke-linecap="round" stroke-linejoin="round" role="img" aria-label="Shovel in a dirt mound">
      <path d="M24 62c6-8 14-11 22-11s16 3 20 11z"/>
      <path d="M30 26l4-4 4 4-4 4z"/>
      <line x1="34" y1="30" x2="46" y2="46"/>
      <path d="M43 45l8-5 5 8-6 6-8-2z"/>
    </svg>
  </div>
  <h3 class="display service-name">Dirt</h3>
  <p class="service-text">Sed ut perspiciatis unde omnis iste natus error sit voluptatem</p>
  <div class="plus"><svg width="52" height="52" viewBox="0 0 52 52"><path d="M26 17v18M17 26h18" stroke="#111" stroke-width="3.5"/></svg></div>
</div>
<div class="abs service featured" style="left:362px;top:1412px">
  <div class="service-icon">
    <svg width="88" height="88" viewBox="0 0 88 88" fill="none" stroke="#5aafd8" stroke-width="1.8" role="img" aria-label="Pile of gravel">
      <circle cx="44" cy="32" r="4"/>
      <circle cx="39" cy="39" r="4"/><circle cx="49" cy="39" r="4"/>
      <circle cx="34" cy="46" r="4"/><circle cx="44" cy="46" r="4"/><circle cx="54" cy="46" r="4"/>
      <circle cx="29" cy="53" r="4"/><circle cx="39" cy="53" r="4"/><circle cx="49" cy="53" r="4"/><circle cx="59" cy="53" r="4"/>
      <line x1="20" y1="59" x2="68" y2="59"/>
      <line x1="26" y1="59" x2="26" y2="63"/><line x1="44" y1="59" x2="44" y2="63"/><line x1="62" y1="59" x2="62" y2="63"/>
    </svg>
  </div>
  <h3 class="display service-name">Gravel</h3>
  <p class="service-text">Sed ut perspiciatis unde omnis iste natus error sit voluptatem</p>
  <div class="plus"><svg width="52" height="52" viewBox="0 0 52 52"><path d="M26 17v18M17 26h18" stroke="#111" stroke-width="3.5"/></svg></div>
</div>
<div class="abs service" style="left:607px;top:1412px">
  <div class="service-icon">
    <svg width="88" height="88" viewBox="0 0 88 88" fill="none" stroke="#1c2b3a" stroke-width="2" stroke-linecap="round" stroke-linejoin="round" role="img" aria-label="Tree stump">
      <ellipse cx="44" cy="26" rx="14" ry="5"/>
      <ellipse cx="44" cy="26" rx="7" ry="2.5"/>
      <path d="M30 26v30l-6 6M58 26v30l6 6"/>
      <path d="M30 56c4 4 24 4 28 0"/>
      <line x1="37" y1="32" x2="37" y2="58"/><line x1="44" y1="33" x2="44" y2="60"/><line x1="51" y1="32" x2="51" y2="58"/>
    </svg>
  </div>
  <h3 class="display service-name">Landscape Bark</h3>
  <p class="service-text">Sed ut perspiciatis unde omnis iste natus error sit voluptatem</p>
  <div class="plus"><svg width="52" height="52" viewBox="0 0 52 52"><path d="M26 17v18M17 26h18" stroke="#111" stroke-width="3.5"/></svg></div>
</div>
<div class="abs service" style="left:853px;top:1412px">
  <div class="service-icon">
    <svg width="88" height="88" viewBox="0 0 88 88" fill="none" stroke="#1c2b3a" stroke-width="2" stroke-linejoin="round" role="img" aria-label="Landscape picture frame">
      <rect x="26" y="30" width="36" height="26" rx="2"/>
      <rect x="22" y="36" width="44" height="14" rx="2"/>
      <rect x="32" y="40" width="24" height="20"/>
      <polyline points="32,58 40,49 46,55 50,51 56,57"/>
      <circle cx="50" cy="45" r="2"/>
    </svg>
  </div>
  <h3 class="display service-name">Landscape Materials</h3>
  <p class="service-text">Sed ut perspiciatis unde omnis iste natus error sit voluptatem</p>
  <div class="plus"><svg width="52" height="52" viewBox="0 0 52 52"><path d="M26 17v18M17 26h18" stroke="#111" stroke-width="3.5"/></svg></div>
</div>

<h2 class="abs display section-title" style="top:1864px">Portfolio</h2>
<div class="tile tile-gravel" role="img" aria-label="Close-up of grey gravel"></div>
<div class="tile tile-forest" role="img" aria-label="Marked tree trunk beside a forest path"></div>
<div class="tile tile-truck" role="img" aria-label="Red semi truck on a country highway"></div>
<div class="tile tile-soil" role="img" aria-label="Grass and soil layer under a blue sky"></div>
<div class="tile tile-coast" role="img" aria-label="Aerial view of a coastal cove with palm trees"></div>
<div class="abs zoom"><svg width="54" height="54" viewBox="0 0 54 54"><circle cx="25" cy="25" r="11" fill="none" stroke="#111" stroke-width="3"/><line x1="33" y1="33" x2="40" y2="40" stroke="#111" stroke-width="3.5" stroke-linecap="round"/></svg></div>

<section class="abs contact-band" role="img" aria-label="Street map of the area"></section>
<div class="abs contact-item" style="left:111px">
  <span class="contact-icon"><svg width="24" height="24" viewBox="0 0 24 24"><path d="M6.6 10.8a15 15 0 0 0 6.6 6.6l2.2-2.2a1 1 0 0 1 1-.25 11.4 11.4 0 0 0 3.6.57 1 1 0 0 1 1 1V20a1 1 0 0 1-1 1A17 17 0 0 1 3 4a1 1 0 0 1 1-1h3.5a1 1 0 0 1 1 1c0 1.25.2 2.45.57 3.57a1 1 0 0 1-.25 1z" fill="#111"/></svg></span>
  +1 999 999 9999
</div>
<div class="abs contact-item" style="left:423px">
  <span class="contact-icon"><svg width="24" height="24" viewBox="0 0 24 24"><rect x="3" y="6" width="18" height="12" fill="#111"/><polyline points="3,6 12,13 21,6" fill="none" stroke="#fff" stroke-width="1.5"/></svg></span>
  hello@ridgelinematerials.com
</div>
<div class="abs contact-item" style="left:854px">
  <span class="contact-icon"><svg width="24" height="24" viewBox="0 0 24 24"><path d="M12 2a7 7 0 0 0-7 7c0 5 7 13 7 13s7-8 7-13a7 7 0 0 0-7-7z" fill="#111"/><circle cx="12" cy="9" r="2.6" fill="#fff"/></svg></span>
  345, Lorem Ipsum
</div>

<input class="abs field" style="left:121px;top:2659px;width:212px" placeholder="Name">
<input class="abs field" style="left:367px;top:2659px;width:213px" placeholder="Email Address">
<input class="abs field" style="left:616px;top:2659px;width:462px" placeholder="Message..">
<a class="abs btn submit">Submit<span class="btn-tab"></span></a>

<footer class="abs footer">
  <div class="brand"><span class="brand-name">Ridgeline Materials</span><span class="brand-mark" style="width:34px;height:34px"></span></div>
  <nav class="footer-menu"><a href="#">Home</a><a href="#">About Us</a><a href="#">Services</a><a href="#">Contact Us</a></nav>
  <div class="socials"><span></span><span></span><span></span></div>
  <div class="footer-rule"></div>
  <p class="copyright">@2023 COPYRIGHTS. RIDGELINE MATERIALS. ALL RIGHTS RESERVED.</p>
</footer>

</body>
</html>
```